Im open to ideas.. I was thinking on my business cards aswell as my logo. a place for my name. email. phone number and abn..

ive attched a file with my business logo. which i dont love the colours.. i was think a dark background with charcoal letters so something along those colour schumes but im open to ideas..

BRM Constructions

```html
<!DOCTYPE html>
<html lang="en">
<head>
<meta charset="utf-8">
<title>BRM Constructions – Business Card</title>
<link rel="stylesheet" href="https://fonts.googleapis.com/css2?family=Open+Sans:wght@400;600;700&display=swap">
<style>
  :root {
    --backdrop: #e7e3e1;
    --card-light: #f1eeed;
    --card-dark: #4e4e4e;
    --ink: #4a4a4a;
    --ink-faint: rgba(74, 74, 74, 0.28);
    --on-dark: #ffffff;
  }
  * { box-sizing: border-box; margin: 0; padding: 0; }
  html, body {
    width: 1200px;
    height: 900px;
    overflow: hidden;
    background: var(--backdrop);
    font-family: "Open Sans", Arial, sans-serif;
  }
  .canvas { position: relative; width: 1200px; height: 900px; }

  .card {
    position: absolute;
    width: 556px;
    height: 343px;
    box-shadow: 0 6px 18px rgba(0, 0, 0, 0.12);
    overflow: hidden;
  }
  .card--front { left: 238px; top: 62px; }
  .card--back  { left: 460px; top: 518px; width: 559px; }

  .card__top {
    height: 185px;
    background: var(--card-light);
    display: flex;
    flex-direction: column;
    align-items: center;
    justify-content: center;
  }
  .card--back .card__top { height: 187px; }
  .card__band {
    position: relative;
    height: calc(100% - 185px);
    background: var(--card-dark);
    color: var(--on-dark);
  }
  .card--back .card__band { height: calc(100% - 187px); }

  .wordmark {
    color: var(--ink);
    font-weight: 700;
    text-align: center;
    line-height: 1;
  }
  .wordmark__main { display: block; font-size: 50px; letter-spacing: 6px; }
  .wordmark__sub { display: block; font-size: 14px; letter-spacing: 7px; margin-top: 6px; }
  .wordmark--faint { color: var(--ink-faint); transform: scaleX(-1); margin-top: 40px; }

  .holder {
    position: absolute;
    right: 316px;
    top: 44px;
    text-align: right;
  }
  .holder__name { font-size: 17px; font-weight: 700; line-height: 22px; }
  .holder__role { font-size: 14px; font-weight: 400; line-height: 22px; }
  .holder__abn { font-size: 15px; font-weight: 700; margin-top: 8px; line-height: 20px; }

  .contacts {
    position: absolute;
    left: 268px;
    top: 45px;
    list-style: none;
  }
  .contacts__item {
    display: flex;
    align-items: center;
    font-size: 15px;
    line-height: 25px;
  }
  .contacts__icon { width: 12px; height: 12px; margin-right: 9px; fill: var(--on-dark); }

  .back__web {
    position: absolute;
    left: 0; right: 0;
    bottom: 28px;
    text-align: center;
    font-size: 15px;
  }
</style>
</head>
<body>
<main class="canvas">
  <section class="card card--front">
    <div class="card__top">
      <div class="wordmark">
        <span class="wordmark__main">BRM</span>
        <span class="wordmark__sub">CONSTRUCTIONS</span>
      </div>
    </div>
    <div class="card__band">
      <div class="holder">
        <p class="holder__name">Daniel Hart</p>
        <p class="holder__role">Managing Director</p>
        <p class="holder__abn">ABN : 31245678</p>
      </div>
      <ul class="contacts">
        <li class="contacts__item">
          <svg class="contacts__icon" viewBox="0 0 24 24" aria-hidden="true"><path d="M6.6 10.8a15.2 15.2 0 0 0 6.6 6.6l2.2-2.2c.3-.3.7-.4 1-.2 1.1.4 2.3.6 3.6.6.6 0 1 .4 1 1V20c0 .6-.4 1-1 1A17 17 0 0 1 3 4c0-.6.4-1 1-1h3.5c.6 0 1 .4 1 1 0 1.3.2 2.5.6 3.6.1.3 0 .7-.2 1z"/></svg>
          044-987 654 321
        </li>
        <li class="contacts__item">
          <svg class="contacts__icon" viewBox="0 0 24 24" aria-hidden="true"><path d="M2 5h20v14H2z M2 5l10 8 10-8" stroke="#4e4e4e" stroke-width="1.5"/></svg>
          hello@brmbuild.com
        </li>
        <li class="contacts__item">
          <svg class="contacts__icon" viewBox="0 0 24 24" aria-hidden="true"><circle cx="12" cy="12" r="10"/><path d="M2 12h20M12 2c3 3 3 17 0 20M12 2c-3 3-3 17 0 20" stroke="#4e4e4e" stroke-width="1.5" fill="none"/></svg>
          www.brmbuild.com
        </li>
      </ul>
    </div>
  </section>

  <section class="card card--back">
    <div class="card__top">
      <div class="wordmark wordmark--faint" aria-hidden="true">
        <span class="wordmark__main">BRM</span>
        <span class="wordmark__sub">CONSTRUCTIONS</span>
      </div>
    </div>
    <div class="card__band">
      <p class="back__web">www.brmbuild.com</p>
    </div>
  </section>
</main>
</body>
</html>
```